Retractable banner.
Health Check For Pets
Check for Ear Mites
Skin Health
Fleas & Ticks

A space SERVE BY <NAME OF CLINIC>

Ideally contain pictures of cats and dogs

```html
<!DOCTYPE html>
<html lang="en">
<head>
<meta charset="utf-8">
<title>Health Check For Pets – Roll-up Banner</title>
<link rel="stylesheet" href="https://fonts.googleapis.com/css2?family=Exo+2:wght@400;600&display=swap">
<style>
  :root {
    --backdrop: #e6e7e9;
    --paper: #ffffff;
    --paper-shade: #eceef0;
    --teal: #4fa9b9;
    --teal-deep: #3f95a6;
    --magenta: #a8198f;
    --photo-cat: #8fa7b0;
    --photo-puppy: #6b7a3c;
    --photo-vet: #b8cbd8;
    --heading-font: "Exo 2", sans-serif;
  }
  html, body {
    margin: 0;
    padding: 0;
    width: 981px;
    height: 1200px;
    overflow: hidden;
    background: var(--backdrop);
  }
  .canvas {
    position: relative;
    width: 981px;
    height: 1200px;
    display: flex;
    align-items: center;
    justify-content: center;
  }
  .banner {
    width: 520px;
    height: 1179px;
    display: block;
    box-shadow: 0 6px 24px rgba(0,0,0,0.18);
  }
  .banner-title {
    font-family: var(--heading-font);
    font-weight: 600;
    font-size: 52px;
    fill: var(--teal);
  }
  .service-item {
    font-family: var(--heading-font);
    font-weight: 400;
    font-size: 29px;
    fill: #ffffff;
  }
</style>
</head>
<body>
<main class="canvas">
  <svg class="banner" viewBox="0 0 495 1122" xmlns="http://www.w3.org/2000/svg">
    <defs>
      <linearGradient id="paperGradient" x1="0" y1="0" x2="1" y2="1">
        <stop offset="0" stop-color="var(--paper)"/>
        <stop offset="1" stop-color="var(--paper-shade)"/>
      </linearGradient>
      <linearGradient id="tealGradient" x1="0" y1="0" x2="0" y2="1">
        <stop offset="0" stop-color="var(--teal)"/>
        <stop offset="1" stop-color="var(--teal-deep)"/>
      </linearGradient>
      <linearGradient id="emblemGradient" x1="0" y1="0" x2="1" y2="1">
        <stop offset="0" stop-color="#f3dff0"/>
        <stop offset="1" stop-color="#dcecef"/>
      </linearGradient>
      <filter id="softShadow" x="-20%" y="-20%" width="140%" height="140%">
        <feDropShadow dx="0" dy="3" stdDeviation="4" flood-color="#000" flood-opacity="0.22"/>
      </filter>
    </defs>

    <!-- background -->
    <rect class="banner-paper" width="495" height="1122" fill="url(#paperGradient)"/>

    <!-- teal field -->
    <path class="teal-field" fill="url(#tealGradient)"
      d="M495,362 L420,385 C250,420 110,430 105,520 C102,600 200,690 245,800 C275,880 285,1000 292,1122 L495,1122 Z"/>

    <!-- magenta swoosh -->
    <g class="swoosh" filter="url(#softShadow)">
      <path d="M505,312 C400,352 220,366 130,386 C35,410 8,470 55,560 C120,680 225,770 256,870 C286,965 298,1040 300,1130"
        fill="none" stroke="var(--paper)" stroke-width="46"/>
      <path d="M505,312 C400,352 220,366 130,386 C35,410 8,470 55,560 C120,680 225,770 256,870 C286,965 298,1040 300,1130"
        fill="none" stroke="var(--magenta)" stroke-width="30"/>
    </g>

    <!-- emblem -->
    <rect class="title-emblem" x="27" y="75" width="131" height="133" rx="10" fill="var(--magenta)"
      role="img" aria-label="Medical cross emblem with cat and dog silhouettes"/>

    <!-- title -->
    <text class="banner-title" x="177" y="128">Health Check</text>
    <text class="banner-title" x="177" y="198">For Pets</text>

    <!-- cat photo -->
    <g class="photo-badge" filter="url(#softShadow)">
      <circle cx="289" cy="390" r="121" fill="var(--magenta)"/>
      <circle cx="277" cy="378" r="118" fill="var(--paper)"/>
    </g>
    <circle cx="277" cy="378" r="110" fill="var(--photo-cat)"
      role="img" aria-label="Photo of a fluffy cat held by a vet in blue scrubs"/>

    <!-- services -->
    <text class="service-item" x="473" y="563" text-anchor="end">•Health Check For Pets</text>
    <text class="service-item" x="473" y="617" text-anchor="end">•Check for Ear Mites</text>
    <text class="service-item" x="473" y="672" text-anchor="end">•Skin Health</text>
    <text class="service-item" x="473" y="727" text-anchor="end">•Fleas &amp; Ticks</text>

    <!-- puppy and kitten photo -->
    <g class="photo-badge" filter="url(#softShadow)">
      <circle cx="132" cy="694" r="92" fill="var(--magenta)"/>
      <circle cx="122" cy="684" r="90" fill="var(--paper)"/>
    </g>
    <circle cx="122" cy="684" r="83" fill="var(--photo-puppy)"
      role="img" aria-label="Photo of a puppy and a kitten on grass"/>

    <!-- vet examining dog photo -->
    <g class="photo-badge" filter="url(#softShadow)">
      <circle cx="372" cy="938" r="112" fill="var(--magenta)"/>
      <circle cx="358" cy="926" r="110" fill="var(--paper)"/>
    </g>
    <circle cx="358" cy="926" r="102" fill="var(--photo-vet)"
      role="img" aria-label="Photo of a vet examining a dog with a stethoscope"/>

    <!-- stethoscope and paw illustration -->
    <rect class="stethoscope-art" x="18" y="825" width="217" height="250" rx="40" fill="url(#emblemGradient)"
      role="img" aria-label="Illustration of a stethoscope with a paw print"/>
  </svg>
</main>
</body>
</html>
```